Modern business card design for professional copywriter

I'd like a business card design that I can use to have my cards printed out by quillprint.com as a squared corners business card (see artwork and design guidelines here: https://help.quillprint.com/hc/en-gb/sections/200570950-QUILL-Product-Templates)

The design should be clean and modern and reflect the colours, tone and branding on my website: https://tessavorrin.com.au

Target Market(s)

Professionals, B2B small business owners

Industry/Entity Type

Business

Contact Information for Business Card

Tessa Vorrin
m: 0468 905 327
e: tessa@tessavorrin.com.au
w: tessavorrin.com.au

Font styles to use
Sans Serif

Requirements
Must have
• Tagline: "Smart copywriting for clever business people"
• Brand colours: fd8000, 009984, 666666 and black
Nice to have

```html
<!DOCTYPE html>
<html lang="en">
<head>
<meta charset="utf-8">
<title>Tessa Vorrin – Business Card</title>
<link rel="stylesheet" href="https://fonts.googleapis.com/css2?family=Jost:wght@400;500&family=Oswald:wght@500&family=Questrial&display=swap">
<style>
  :root {
    --brand-orange: #fd8000;
    --brand-teal: #009984;
    --brand-grey: #666666;
    --card-black: #1b1b1b;
    --stage: #2a2a2a;
    --ink-light: #f2f2f2;
  }
  * { box-sizing: border-box; margin: 0; padding: 0; }
  html, body { width: 1200px; height: 900px; overflow: hidden; }
  body {
    background: var(--stage);
    position: relative;
    font-family: "Jost", sans-serif;
  }
  .card {
    position: absolute;
    left: 300px;
    width: 600px;
    height: 392px;
    background: var(--card-black);
    overflow: hidden;
  }
  .card--front { top: 38px; }
  .card--back  { top: 470px; }
  .card__band {
    position: absolute;
    left: 0; right: 0; bottom: 0;
    height: 10px;
    background: var(--brand-orange);
  }

  /* Front */
  .brand {
    position: absolute;
    top: 118px;
    left: 0; right: 0;
    text-align: center;
  }
  .brand__name {
    display: inline-flex;
    align-items: center;
    gap: 14px;
    font-family: "Questrial", sans-serif;
    font-size: 54px;
    color: var(--brand-grey);
    line-height: 1;
  }
  .brand__mark {
    width: 18px; height: 18px;
    border-radius: 50%;
    background: var(--brand-grey);
  }
  .brand__role {
    margin-top: 6px;
    font-family: "Questrial", sans-serif;
    font-size: 14px;
    letter-spacing: 8px;
    color: var(--brand-grey);
    text-transform: uppercase;
    padding-left: 140px;
  }
  .tagline {
    position: absolute;
    top: 300px;
    left: 0; right: 0;
    text-align: center;
    font-size: 17px;
    letter-spacing: 1.5px;
    color: var(--brand-grey);
  }

  /* Back */
  .identity {
    position: absolute;
    top: 140px;
    right: 338px;
    text-align: right;
  }
  .identity__name {
    font-family: "Oswald", sans-serif;
    font-weight: 500;
    font-size: 40px;
    line-height: 1.05;
    color: var(--brand-orange);
    text-transform: uppercase;
  }
  .identity__role {
    font-size: 21px;
    letter-spacing: 1px;
    color: var(--ink-light);
  }
  .divider {
    position: absolute;
    top: 142px;
    left: 286px;
    width: 2px;
    height: 88px;
    background: var(--brand-teal);
  }
  .contacts {
    position: absolute;
    top: 140px;
    left: 308px;
    list-style: none;
  }
  .contacts__item {
    display: flex;
    align-items: center;
    gap: 12px;
    height: 29px;
    font-size: 17px;
    letter-spacing: 1.2px;
    color: var(--ink-light);
  }
  .contacts__icon { width: 16px; height: 16px; flex: none; }
</style>
</head>
<body>

<section class="card card--front" aria-label="Card front">
  <div class="brand">
    <div class="brand__name"><span class="brand__mark"></span>Tessa Vorrin</div>
    <div class="brand__role">Copywriter</div>
  </div>
  <p class="tagline">Smart copywriting for clever business people</p>
  <div class="card__band"></div>
</section>

<section class="card card--back" aria-label="Card back">
  <div class="identity">
    <h1 class="identity__name">Tessa Vorrin</h1>
    <p class="identity__role">Copywriter</p>
  </div>
  <div class="divider"></div>
  <ul class="contacts">
    <li class="contacts__item">
      <svg class="contacts__icon" viewBox="0 0 16 16" aria-hidden="true">
        <rect x="4" y="1" width="8" height="14" rx="1.5" fill="none" stroke="#fd8000" stroke-width="1.6"/>
        <line x1="7" y1="12.5" x2="9" y2="12.5" stroke="#fd8000" stroke-width="1.4"/>
      </svg>
      0468 905 327
    </li>
    <li class="contacts__item">
      <svg class="contacts__icon" viewBox="0 0 16 16" aria-hidden="true">
        <rect x="1" y="3.5" width="14" height="9.5" fill="#fd8000"/>
        <polyline points="1,3.5 8,9 15,3.5" fill="none" stroke="#1b1b1b" stroke-width="1.4"/>
      </svg>
      tessa@tessavorrin.com.au
    </li>
    <li class="contacts__item">
      <svg class="contacts__icon" viewBox="0 0 16 16" aria-hidden="true">
        <circle cx="6.5" cy="6.5" r="4.5" fill="none" stroke="#fd8000" stroke-width="2"/>
        <line x1="10" y1="10" x2="14.5" y2="14.5" stroke="#fd8000" stroke-width="2.2" stroke-linecap="round"/>
      </svg>
      tessavorrin.com.au
    </li>
  </ul>
  <div class="card__band"></div>
</section>

</body>
</html>
```